Business Card Design

Company is a Commercial Building Company specialising in New Construction and existing refurbishments

Industry/Entity Type

Business

Contact Information for Business Card

Liam Porter
Construction Manager
E Liam@marshbuilding.com.au
M 0400 213 594
Mail 14 Tarrant Rise Halden Bay WA 6400

```html
<!DOCTYPE html>
<html lang="en">
<head>
<meta charset="utf-8">
<title>Marsh Building &amp; Construction – Business Card</title>
<link rel="stylesheet" href="https://fonts.googleapis.com/css2?family=Roboto:wght@300;400;700&display=swap">
<style>
  :root {
    --bg: #e9e7e4;
    --card: #ffffff;
    --ink: #1d1f24;
    --navy: #2a2e3c;
    --orange: #f28a1e;
    --blue: #1bb3d1;
    --shadow: rgba(0, 0, 0, 0.12);
  }
  * { box-sizing: border-box; margin: 0; padding: 0; }
  html, body {
    width: 1200px;
    height: 1023px;
    overflow: hidden;
    background: var(--bg);
    font-family: "Roboto", Arial, sans-serif;
    color: var(--ink);
  }
  .canvas {
    position: relative;
    width: 1200px;
    height: 1023px;
  }
  .card {
    position: absolute;
    left: 240px;
    width: 720px;
    height: 440px;
    background: var(--card);
    box-shadow: 0 6px 20px var(--shadow);
  }
  .card--front { top: 50px; }
  .card--back { top: 533px; }

  /* Brand name */
  .brand {
    display: flex;
    align-items: center;
    gap: 14px;
  }
  .brand__mark {
    width: 22px;
    height: 22px;
    background: var(--orange);
    flex: none;
  }
  .brand__name {
    font-weight: 700;
    color: var(--navy);
    font-size: 26px;
    line-height: 1.1;
    letter-spacing: 0.5px;
    text-transform: uppercase;
  }
  .card--front .brand {
    position: absolute;
    right: 70px;
    top: 96px;
  }

  /* Person */
  .person {
    position: absolute;
    left: 60px;
    top: 290px;
  }
  .person__name {
    font-weight: 300;
    font-size: 34px;
    line-height: 1.1;
  }
  .person__role {
    font-weight: 300;
    font-size: 17px;
    margin-top: 4px;
  }

  /* Contacts */
  .contacts {
    position: absolute;
    left: 370px;
    top: 282px;
    list-style: none;
    font-weight: 300;
    font-size: 17px;
    line-height: 24px;
  }
  .contacts__item {
    display: flex;
    align-items: flex-start;
    gap: 12px;
  }
  .contacts__icon {
    width: 14px;
    height: 14px;
    margin-top: 5px;
    flex: none;
    fill: var(--ink);
  }

  /* Back */
  .accent-line {
    position: absolute;
    left: 50%;
    width: 3px;
    margin-left: -1.5px;
  }
  .accent-line--top { top: 0; height: 150px; background: var(--orange); }
  .accent-line--bottom { bottom: 0; height: 150px; background: var(--blue); }
  .card--back .brand {
    position: absolute;
    left: 0;
    right: 0;
    top: 196px;
    justify-content: center;
  }
</style>
</head>
<body>
<main class="canvas">

  <section class="card card--front" aria-label="Business card front">
    <div class="brand">
      <span class="brand__mark"></span>
      <span class="brand__name">Marsh Building<br>&amp; Construction</span>
    </div>

    <div class="person">
      <p class="person__name">Liam Porter</p>
      <p class="person__role">Construction Manager</p>
    </div>

    <ul class="contacts">
      <li class="contacts__item">
        <svg class="contacts__icon" viewBox="0 0 14 14" aria-hidden="true"><rect x="3" y="0" width="8" height="14" rx="1.5"/><rect x="4.5" y="2" width="5" height="8" fill="#fff"/></svg>
        <span>0400 213 594</span>
      </li>
      <li class="contacts__item">
        <svg class="contacts__icon" viewBox="0 0 14 14" aria-hidden="true"><rect x="0" y="2" width="14" height="10"/><path d="M0.8 2.8 L7 8 L13.2 2.8" stroke="#fff" stroke-width="1.4" fill="none"/></svg>
        <span>Liam@marshbuilding.com.au</span>
      </li>
      <li class="contacts__item">
        <svg class="contacts__icon" viewBox="0 0 14 14" aria-hidden="true"><path d="M7 0 C3.7 0 1.5 2.4 1.5 5.3 C1.5 9 7 14 7 14 C7 14 12.5 9 12.5 5.3 C12.5 2.4 10.3 0 7 0 Z"/><circle cx="7" cy="5.3" r="2" fill="#fff"/></svg>
        <span>14 Tarrant Rise<br>Halden Bay WA 6400</span>
      </li>
    </ul>
  </section>

  <section class="card card--back" aria-label="Business card back">
    <span class="accent-line accent-line--top"></span>
    <div class="brand">
      <span class="brand__mark"></span>
      <span class="brand__name">Marsh Building<br>&amp; Construction</span>
    </div>
    <span class="accent-line accent-line--bottom"></span>
  </section>

</main>
</body>
</html>
```